RW Framewell Inc Business cards

We need business cards using our existing logo but slightly modified. Right now the logo says RW Loadbearing Masonry. We want to keep the RW part of the design, but replace the Structural Concrete portion with "FRAMEWELL". Please see the attached file.
Ideally this would be a blank template so we can add Different Names, titles, and phone numbers later.
On the one side we want only the logo and on the other side the detail. I'm attaching an example for you to see.
Please reach out with any other questions. Our address and other details will be given out once we find a design we like.

Target Market(s)

Construction Industry

```html
<!DOCTYPE html>
<html lang="en">
<head>
<meta charset="UTF-8">
<title>RW Framewell Inc – Business Cards</title>
<link rel="stylesheet" href="https://fonts.googleapis.com/css2?family=Roboto:wght@400;500;700&display=swap">
<style>
  :root {
    --brand-blue: #1177bf;
    --paper: #ffffff;
    --backdrop: #e8e8e9;
    --ink: #333333;
    --divider: #b9b9b9;
    --shadow: rgba(0, 0, 0, 0.18);
  }
  * { box-sizing: border-box; }
  html, body {
    margin: 0;
    width: 1200px;
    height: 900px;
    overflow: hidden;
    background: var(--backdrop);
    font-family: "Roboto", Arial, sans-serif;
  }
  .canvas {
    position: relative;
    width: 1200px;
    height: 900px;
  }
  .card {
    position: absolute;
    left: 300px;
    width: 600px;
    height: 343px;
    box-shadow: 0 10px 24px var(--shadow), 0 2px 4px rgba(0,0,0,0.08);
  }
  .card--front {
    top: 70px;
    background: var(--brand-blue);
    display: flex;
    align-items: center;
    justify-content: center;
  }
  .wordmark {
    display: flex;
    align-items: center;
    gap: 16px;
    color: var(--paper);
    font-weight: 500;
  }
  .wordmark__square {
    width: 22px;
    height: 22px;
    background: var(--paper);
  }
  .wordmark__name {
    font-size: 40px;
    letter-spacing: 8px;
    line-height: 1;
  }
  .card--back {
    top: 487px;
    background: var(--paper);
    display: flex;
    align-items: center;
    justify-content: center;
    gap: 26px;
  }
  .identity {
    text-align: right;
    color: var(--ink);
    font-size: 15px;
    line-height: 1.3;
  }
  .identity__name {
    color: var(--brand-blue);
    font-weight: 700;
    font-size: 25px;
    line-height: 1.1;
    margin-bottom: 2px;
  }
  .divider {
    width: 1px;
    height: 150px;
    background: linear-gradient(to bottom, transparent, var(--divider) 25%, var(--divider) 75%, transparent);
  }
  .contacts {
    list-style: none;
    margin: 0;
    padding: 0;
    color: var(--ink);
    font-size: 15px;
    line-height: 1.45;
  }
  .contacts__item {
    display: flex;
    align-items: center;
    gap: 7px;
  }
  .contacts__icon {
    width: 12px;
    height: 12px;
    flex: none;
    fill: var(--brand-blue);
  }
</style>
</head>
<body>
  <main class="canvas">
    <section class="card card--front" aria-label="Card front">
      <div class="wordmark">
        <span class="wordmark__square"></span>
        <span class="wordmark__name">RW FRAMEWELL</span>
      </div>
    </section>

    <section class="card card--back" aria-label="Card back">
      <div class="identity">
        <div class="identity__name">DARREN HOLLIS</div>
        <div class="identity__title">Owner/CEO</div>
        <div class="identity__address">1480 N Ridgeline Road</div>
        <div class="identity__address">Harlow County 6108</div>
      </div>
      <div class="divider"></div>
      <ul class="contacts">
        <li class="contacts__item">
          <svg class="contacts__icon" viewBox="0 0 12 12" aria-hidden="true"><path d="M3 0h6a1 1 0 0 1 1 1v10a1 1 0 0 1-1 1H3a1 1 0 0 1-1-1V1a1 1 0 0 1 1-1zm0 2v7h6V2z"/></svg>
          555-201-7784
        </li>
        <li class="contacts__item">
          <svg class="contacts__icon" viewBox="0 0 12 12" aria-hidden="true"><path d="M2.5 0.5l2 2.5-1 1.2c.7 1.6 2 2.9 3.6 3.6l1.2-1 2.5 2-1.3 2.2C5 10.6 1.4 7 .6 1.8z"/></svg>
          555-318-2046
        </li>
        <li class="contacts__item">
          <svg class="contacts__icon" viewBox="0 0 12 12" aria-hidden="true"><path d="M0 2h12v8H0zm1 1v.4l5 3.2 5-3.2V3z"/></svg>
          info@rwframewell.com
        </li>
        <li class="contacts__item">
          <svg class="contacts__icon" viewBox="0 0 12 12" aria-hidden="true"><circle cx="6" cy="6" r="6"/></svg>
          www.rwframewell.com
        </li>
      </ul>
    </section>
  </main>
</body>
</html>
```